Kestrel Facilities Business Card Design

We would now like to design business cards with the new Kestrel Facilities logo

Target Market(s)

Professional

Industry/Entity Type

Professional services

Contact Information for Business Card

Employee name, title, phone number, email address, corporate office address and logo.

Font styles to use
Sans Serif

Colors
0054AA
0677BA
7BADD7
CADEEF
E8F1F8

Requirements
Must have
• My logo
Should not have
• any other pictures or images besides my logo

```html
<!DOCTYPE html>
<html lang="en">
<head>
<meta charset="utf-8">
<title>Kestrel Facilities Business Card</title>
<link rel="stylesheet" href="https://fonts.googleapis.com/css2?family=Oswald:wght@500&family=Arimo:wght@400&display=swap">
<style>
  :root {
    --backdrop: #1e1e1f;
    --card: #0b0b0c;
    --brand-blue: #0a80e6;
    --text-light: #e6e6e6;
    --divider: #2c2c2e;
  }
  * { margin: 0; padding: 0; box-sizing: border-box; }
  html, body {
    width: 1200px; height: 900px; overflow: hidden;
    background: var(--backdrop);
  }
  .canvas {
    position: relative; width: 1200px; height: 900px;
  }
  .card {
    position: absolute; left: 320px;
    width: 560px; height: 320px;
    background: var(--card);
    box-shadow: 0 12px 30px rgba(0,0,0,0.55);
  }
  .card--back { top: 100px; }
  .card--front { top: 480px; }

  .brand {
    display: flex; align-items: center; gap: 14px;
    color: var(--brand-blue);
    font-family: "Oswald", sans-serif; font-weight: 500;
    text-transform: uppercase; line-height: 1.05;
  }
  .brand__mark {
    border: 5px solid var(--brand-blue);
    flex: none;
  }
  .card--back .brand {
    position: absolute; left: 50%; top: 50%;
    transform: translate(-50%, -50%);
    font-size: 40px; letter-spacing: 2px;
  }
  .card--back .brand__mark { width: 74px; height: 74px; }

  .card--front .brand {
    position: absolute; left: 40px; top: 50%;
    transform: translateY(-50%);
    font-size: 27px; letter-spacing: 1px;
  }
  .card--front .brand__mark { width: 52px; height: 52px; border-width: 4px; }

  .card__divider {
    position: absolute; left: 250px; top: 0; bottom: 0;
    width: 1px; background: var(--divider);
  }
  .contact {
    position: absolute; left: 282px; top: 62px;
    font-family: "Arimo", sans-serif; color: var(--text-light);
    font-size: 15px; line-height: 1.3;
  }
  .contact__name {
    font-family: "Oswald", sans-serif; font-weight: 500;
    color: var(--brand-blue); font-size: 27px;
    text-transform: uppercase; letter-spacing: 0.3px; line-height: 1.1;
  }
  .contact__title { font-size: 15px; margin-bottom: 14px; }
  .contact__list { list-style: none; }
  .contact__item { display: flex; align-items: center; gap: 8px; margin-bottom: 3px; }
  .contact__icon { width: 14px; height: 14px; flex: none; }
  .contact__accent { color: var(--brand-blue); }
  .contact__address { margin-top: 16px; }
</style>
</head>
<body>
<main class="canvas">

  <section class="card card--back" aria-label="Business card back">
    <div class="brand">
      <span class="brand__mark" aria-hidden="true"></span>
      <span class="brand__name">Kestrel<br>Facilities</span>
    </div>
  </section>

  <section class="card card--front" aria-label="Business card front">
    <div class="brand">
      <span class="brand__mark" aria-hidden="true"></span>
      <span class="brand__name">Kestrel<br>Facilities</span>
    </div>
    <div class="card__divider"></div>
    <div class="contact">
      <p class="contact__name">Daniel Rowe</p>
      <p class="contact__title">Managing Director</p>
      <ul class="contact__list">
        <li class="contact__item">
          <svg class="contact__icon" viewBox="0 0 24 24" aria-hidden="true">
            <path fill="var(--brand-blue)" d="M6.6 10.8a15.1 15.1 0 0 0 6.6 6.6l2.2-2.2a1 1 0 0 1 1-.25 11.4 11.4 0 0 0 3.6.57 1 1 0 0 1 1 1V20a1 1 0 0 1-1 1A17 17 0 0 1 3 4a1 1 0 0 1 1-1h3.5a1 1 0 0 1 1 1c0 1.25.2 2.45.57 3.57a1 1 0 0 1-.25 1z"/>
          </svg>
          <span>044-987 650 312</span>
        </li>
        <li class="contact__item">
          <svg class="contact__icon" viewBox="0 0 24 24" aria-hidden="true">
            <rect x="2" y="5" width="20" height="14" fill="var(--brand-blue)"/>
            <path d="M2 5l10 8 10-8" fill="none" stroke="var(--card)" stroke-width="2"/>
          </svg>
          <span>info@kestrelfm.com</span>
        </li>
        <li class="contact__item">
          <svg class="contact__icon" viewBox="0 0 24 24" aria-hidden="true">
            <g fill="none" stroke="var(--brand-blue)" stroke-width="2">
              <circle cx="12" cy="12" r="10"/>
              <ellipse cx="12" cy="12" rx="4" ry="10"/>
              <path d="M2 12h20M4 7h16M4 17h16"/>
            </g>
          </svg>
          <span>www.<span class="contact__accent">kestrelfm</span>.com</span>
        </li>
      </ul>
      <p class="contact__address">18, Harbour Lane, Suite 4<br>30715, Northland</p>
    </div>
  </section>

</main>
</body>
</html>
```